Parcelwise HQ letterhead and envelope

Design a formal (8.5x11) letterhead and envelope for sales outreach and legal matters. Using design input from https://www.parcelwisehq.example/ and the attached documents.

Industry/Entity Type

Software Service

Requirements
Must have
• These 4 hex colors are our official colors:
• #355c98 [blue]
• #1eb1a2 [teal]
• #fdba12 [gold]
• #f1653b [orange]
• So no other colors besides these should be used.

```html
<!DOCTYPE html>
<html lang="en">
<head>
<meta charset="utf-8">
<title>Parcelwise HQ Letterhead</title>
<link href="https://fonts.googleapis.com/css2?family=Source+Sans+3:wght@300;400;600;700&display=swap" rel="stylesheet">
<style>
  :root {
    --blue: #355c98;
    --teal: #1eb1a2;
    --ink: #2a2a2a;
    --paper: #ffffff;
    --backdrop: #e4e5e7;
  }
  * { box-sizing: border-box; margin: 0; padding: 0; }
  html, body { width: 1200px; height: 945px; overflow: hidden; }
  body {
    background: var(--backdrop);
    font-family: "Source Sans 3", sans-serif;
    position: relative;
  }
  .letterhead {
    position: absolute;
    left: 260px; top: 32px;
    width: 680px; height: 880px;
    background: var(--paper);
    box-shadow: 0 4px 18px rgba(0,0,0,0.12);
    overflow: hidden;
  }
  .top-rule { position: absolute; left: 0; top: 0; width: 100%; height: 5px; background: var(--teal); }
  .brand {
    position: absolute; left: 52px; top: 44px;
    display: flex; align-items: center; gap: 10px;
  }
  .brand-dot { width: 26px; height: 26px; border-radius: 50%; border: 3px solid var(--blue); }
  .brand-name { font-size: 24px; font-weight: 300; color: var(--blue); letter-spacing: 0.5px; }
  .letter-body {
    position: absolute; left: 90px; top: 180px; width: 520px;
    color: var(--ink); font-size: 12.5px; line-height: 1.35;
  }
  .salutation { font-weight: 700; font-size: 15px; margin-bottom: 14px; }
  .letter-body p { margin-bottom: 16px; }
  .signature {
    position: absolute; left: 110px; top: 650px;
    width: 130px; height: 50px; background: #eceef1; border-radius: 4px;
  }
  .corner-mark {
    position: absolute; right: 48px; top: 742px;
    width: 54px; height: 54px; border-radius: 50%; background: var(--teal);
  }
  .footer-rule {
    position: absolute; left: 0; top: 766px; width: 100%; height: 5px;
    background: var(--teal);
  }
  .footer-rule.lower { top: 856px; background: linear-gradient(90deg, var(--blue), var(--teal)); }
  .contacts {
    position: absolute; left: 52px; top: 790px;
    font-size: 12px; color: var(--ink);
    display: grid; gap: 10px;
  }
  .contact-row { display: flex; gap: 18px; }
  .contact { display: flex; align-items: center; gap: 5px; }
  .contact svg { width: 11px; height: 11px; fill: var(--blue); }
</style>
</head>
<body>
<main class="letterhead">
  <div class="top-rule"></div>
  <header class="brand">
    <span class="brand-dot"></span>
    <span class="brand-name">Parcelwise HQ</span>
  </header>

  <section class="letter-body">
    <p class="salutation">Dear Mr. Harlow,</p>
    <p>Lorem Ipsum is simply dummy text of the printing and typesetting industry. Lorem Ipsum has been the industry's standard dummy text ever since the 1500s, when an unknown printer took a galley of type and scrambled it to make a type specimen book. It has survived not only five centuries, but also the leap into electronic typesetting, remaining essentially unchanged.</p>
    <p>The standard chunk of Lorem Ipsum used since the 1500s is reproduced below for those interested. Sections 1.10.32 and 1.10.33 from "de Finibus Bonorum et Malorum" by Cicero are also reproduced in their exact original form, accompanied by English versions from the 1914 translation by H. Rackham</p>
    <p>Lorem Ipsum is simply dummy text of the printing and typesetting industry. Lorem Ipsum has been the industry's standard dummy text ever since the 1500s, when an unknown printer took a galley of type and scrambled it to make a type specimen book. It has survived not only five centuries, but also the leap into electronic typesetting, remaining essentially unchanged. It was popularised in the</p>
    <p>The standard chunk of Lorem Ipsum used since the 1500s is reproduced below for those interested. Sections 1.10.32 and 1.10.33 from "de Finibus Bonorum et Malorum" by Cicero are also reproduced in their exact original form, accompanied by English versions from the 1914 translation by H. Rackham</p>
    <p>The standard chunk of Lorem Ipsum used since the 1500s is reproduced below for those interested. Sections 1.10.32 and 1.10.33 from "de Finibus Bonorum et Malorum" by Cicero are also reproduced in their exact original form.</p>
  </section>

  <div class="signature" role="img" aria-label="Handwritten signature of the sender"></div>

  <div class="footer-rule"></div>
  <div class="corner-mark"></div>

  <footer class="contacts">
    <div class="contact-row">
      <span class="contact"><svg viewBox="0 0 24 24"><path d="M6.6 10.8a15 15 0 0 0 6.6 6.6l2.2-2.2a1 1 0 0 1 1-.25 11.4 11.4 0 0 0 3.6.57 1 1 0 0 1 1 1V20a1 1 0 0 1-1 1A17 17 0 0 1 3 4a1 1 0 0 1 1-1h3.5a1 1 0 0 1 1 1c0 1.25.2 2.45.57 3.57a1 1 0 0 1-.25 1z"/></svg>(555) 210-4417</span>
      <span class="contact"><svg viewBox="0 0 24 24"><path d="M2 5h20v14H2zm2 2v.5l8 5 8-5V7z"/></svg>jsmith@parcelwisehq.example</span>
      <span class="contact"><svg viewBox="0 0 24 24"><circle cx="12" cy="12" r="10"/></svg>www.parcelwisehq.example</span>
    </div>
    <div class="contact-row">
      <span class="contact"><svg viewBox="0 0 24 24"><path d="M6.6 10.8a15 15 0 0 0 6.6 6.6l2.2-2.2a1 1 0 0 1 1-.25 11.4 11.4 0 0 0 3.6.57 1 1 0 0 1 1 1V20a1 1 0 0 1-1 1A17 17 0 0 1 3 4a1 1 0 0 1 1-1h3.5a1 1 0 0 1 1 1c0 1.25.2 2.45.57 3.57a1 1 0 0 1-.25 1z"/></svg>(555) 388-9021</span>
      <span class="contact"><svg viewBox="0 0 24 24"><path d="M12 2a7 7 0 0 0-7 7c0 5 7 13 7 13s7-8 7-13a7 7 0 0 0-7-7zm0 9.5A2.5 2.5 0 1 1 12 6.5a2.5 2.5 0 0 1 0 5z"/></svg>82 Lantern Row Fairview, OH 40000</span>
    </div>
  </footer>
  <div class="footer-rule lower"></div>
</main>
</body>
</html>
```